Professional and creative business card design for recruiting service providers

Our company supports German medium-sized companies in filling vacancies promptly. For this we use social media marketing and bring our customers into the visibility.

We want a professional but also creative design for our business cards.

Please look at lindqvar-staff.de to get an impression of our CI.

Target Market(s)

Small and medium-sized companies in Germany from the industry

Industry/Entity Type

Industrie, Handwerk

Contact Information for Business Card

Name, Position, Telefonnummer, Email, Website

Colors
EE7325
F08F49
F5BC92
FAE3D3
FDF4ED

Requirements
Must have
• A picture of the employee and in the style of www.lindqvar-staff.de

```html
<!DOCTYPE html>
<html lang="de">
<head>
<meta charset="utf-8">
<title>Lindqvar &amp; Staff – Business Card</title>
<link rel="stylesheet" href="https://fonts.googleapis.com/css2?family=Montserrat:wght@700&family=Arimo:wght@400;700&display=swap">
<style>
  :root {
    --bg: #2b2b2b;
    --card: #0d0d0d;
    --orange: #ee5a2a;
    --white: #ffffff;
    --muted: #8a8a8a;
    --photo-dark: #1a1a1e;
    --photo-mid: #3a3a44;
  }
  * { margin: 0; padding: 0; box-sizing: border-box; }
  html, body { width: 1200px; height: 900px; overflow: hidden; }
  body {
    background: var(--bg);
    display: flex;
    flex-direction: column;
    align-items: center;
    justify-content: center;
    gap: 40px;
  }
  .card {
    position: relative;
    width: 700px;
    height: 400px;
    background: var(--card);
    overflow: hidden;
    box-shadow: 0 10px 30px rgba(0,0,0,.5);
  }
  .card__band {
    position: absolute;
    left: 0; right: 0; bottom: 0;
    height: 14px;
    background: var(--orange);
  }
  .brand {
    position: absolute;
    display: flex;
    align-items: center;
    gap: 18px;
  }
  .brand__mark {
    width: 62px; height: 62px;
    background: var(--orange);
  }
  .brand__name {
    font-family: "Montserrat", sans-serif;
    font-weight: 700;
    color: var(--white);
    letter-spacing: 3px;
    line-height: 1.1;
    font-size: 30px;
  }
  .brand__name span { display: block; }

  /* front */
  .card--front .brand { left: 270px; top: 70px; }
  .photo {
    position: absolute;
    left: 40px; bottom: 14px;
    width: 260px; height: 300px;
    background: radial-gradient(ellipse at 50% 30%, var(--photo-mid), var(--photo-dark) 70%);
  }
  .person {
    position: absolute;
    left: 340px; top: 200px;
    font-family: "Arimo", sans-serif;
  }
  .person__name {
    color: var(--orange);
    font-weight: 700;
    font-size: 26px;
    letter-spacing: .5px;
  }
  .person__role {
    color: var(--white);
    font-size: 19px;
    margin-top: 2px;
  }
  .divider {
    position: absolute;
    left: 318px; top: 270px;
    width: 1px; height: 100px;
    background: var(--muted);
  }
  .contact {
    position: absolute;
    left: 340px; top: 280px;
    list-style: none;
    font-family: "Arimo", sans-serif;
    font-size: 19px;
    color: var(--white);
  }
  .contact li {
    display: flex;
    align-items: center;
    gap: 10px;
    height: 30px;
  }
  .contact svg { width: 18px; height: 18px; flex: none; }
  .accent { color: var(--orange); }

  /* back */
  .card--back .brand {
    left: 50%; top: 50%;
    transform: translate(-50%, -55%);
  }
  .card--back .brand__mark { width: 80px; height: 80px; }
  .card--back .brand__name { font-size: 38px; }
</style>
</head>
<body>

<section class="card card--front">
  <div class="photo" role="img" aria-label="Portrait photo of the employee"></div>

  <div class="brand">
    <div class="brand__mark"></div>
    <div class="brand__name"><span>LINDQVAR</span><span>&amp; STAFF</span></div>
  </div>

  <div class="person">
    <p class="person__name">MARTEN HOLLOWAY</p>
    <p class="person__role">Managing Director</p>
  </div>

  <div class="divider"></div>

  <ul class="contact">
    <li>
      <svg viewBox="0 0 24 24" aria-hidden="true"><path fill="#ee5a2a" d="M6.6 10.8a15 15 0 0 0 6.6 6.6l2.2-2.2c.3-.3.7-.4 1-.2 1.1.4 2.3.6 3.6.6.6 0 1 .4 1 1V20c0 .6-.4 1-1 1A17 17 0 0 1 3 4c0-.6.4-1 1-1h3.5c.6 0 1 .4 1 1 0 1.3.2 2.5.6 3.6.1.3 0 .7-.2 1z"/></svg>
      030-555 014 722
    </li>
    <li>
      <svg viewBox="0 0 24 24" aria-hidden="true"><path fill="#ee5a2a" d="M2 5h20v14H2z"/><path fill="none" stroke="#0d0d0d" stroke-width="2" d="M2 5l10 8 10-8"/></svg>
      info@lindqvar-staff.de
    </li>
    <li>
      <svg viewBox="0 0 24 24" aria-hidden="true"><g fill="none" stroke="#ee5a2a" stroke-width="2"><circle cx="12" cy="12" r="9"/><ellipse cx="12" cy="12" rx="4" ry="9"/><path d="M3 12h18M5 7h14M5 17h14"/></g></svg>
      <span>www.<span class="accent">lindqvar-staff</span>.de</span>
    </li>
  </ul>

  <div class="card__band"></div>
</section>

<section class="card card--back">
  <div class="brand">
    <div class="brand__mark"></div>
    <div class="brand__name"><span>LINDQVAR</span><span>&amp; STAFF</span></div>
  </div>
  <div class="card__band"></div>
</section>

</body>
</html>
```